Graphical Enhancement of Existing WordPress Website, 4 Landing Pages and 5 Social Sites

This project involves graphically enhancing already existing web pages. The website, landing pages and social pages were developed in the last couple of months using WordPress.
We have a newly developed website (20 - 30 pages), 4 landing pages and 5 social sites. The website has one design for the home page and one different design for most of the secondary pages with varying graphics. The 4 landing pages are identical except for one photo per page and two colors. The 5 social sites are not yet complete but will be soon.
The look and feel of all of these is OK but not great. We want the pages revised by a graphic designer/web designer so that they look very, very pleasing. We want to convey a feeling of business polish, smart, but not heavy corporate. The images for individual pages should reinforce the content of the page. The layout and function of the main website and landing pages would probably not change significantly but we are open to suggestion. Primarily we just want to go from OK looking to great looking. This might involve primarily improvements to the colors, fonts and/or images.
Lastly, some designers/developers prefer email and do not like talking much. We require the ability to talk frequenlty, probably on Skype.
Please submit one graphical enhancement of this page:
http://www.parcelnorth-check.example/
and one graphical enhancement of this page:
http://www.brivolt.example/web/
Reason: I would like to see more designs.
I can absolutley guarantee payment and would be happy to escrow the funds if I see a design I like.
Reason: We found a design we liked and tried to communicate with the designer. The designer has been unresponsive for a week or two. We can't hire someone who does not respond.
Target Market(s)
We sell software to large companies (Meridian 400). Potential customers for our software are large enterprises with large CRM deployments in the US and Canada.
Industry/Entity Type
Business
Look and feel

```html
<!DOCTYPE html>
<html lang="en">
<head>
<meta charset="utf-8">
<title>Brivolt Data — Blog</title>
<link href="https://fonts.googleapis.com/css2?family=Pontano+Sans&family=Roboto:wght@300;400;500;700&display=swap" rel="stylesheet">
<style>
:root{
  --navy:#2b3a78;
  --navy-dark:#1f2c63;
  --gold:#f5b81c;
  --ink:#333333;
  --muted:#777777;
  --topbar:#2e3033;
  --footer:#3b3c3e;
  --footer-deep:#2b2c2e;
  --rule:#d6d6d6;
  --panel:#e2e2e2;
}
*{box-sizing:border-box;margin:0;padding:0}
html,body{width:892px;height:1200px;overflow:hidden;background:#fff}
body{position:relative;font-family:"Pontano Sans",sans-serif;color:var(--ink)}
.abs{position:absolute}

.topbar{left:0;top:0;width:892px;height:22px;background:var(--topbar)}
.topbar .contact{position:absolute;top:5px;font-size:10px;color:var(--gold);display:flex;align-items:center;gap:5px}
.social{position:absolute;top:5px;left:760px;display:flex;gap:9px}
.social span{width:12px;height:12px;border-radius:50%;background:#bfc1c4;display:block}

.header{left:0;top:22px;width:892px;height:63px;background:linear-gradient(#ffffff,#f1f1f1)}
.brand{position:absolute;left:38px;top:12px;display:flex;align-items:center;gap:8px}
.brand .mark{width:26px;height:26px;border-radius:50%;background:var(--navy)}
.brand .name{font-family:"Roboto",sans-serif;font-weight:500;font-size:24px;color:var(--navy);line-height:1}
.brand .tag{position:absolute;left:68px;top:31px;font-size:9px;color:#222;white-space:nowrap}
.nav{position:absolute;top:24px;right:29px;display:flex;gap:20px;font-family:"Roboto",sans-serif;font-size:11.5px;color:#333}
.nav .current{color:var(--navy);font-weight:500}

.banner{left:0;top:85px;width:892px;height:88px;background:linear-gradient(100deg,#2a3775,#33458c 55%,#2a3775)}
.banner h1{position:absolute;right:30px;top:30px;font-family:"Roboto",sans-serif;font-weight:400;font-size:24px;color:var(--gold)}
.banner-rule{left:0;top:173px;width:892px;height:4px;background:var(--gold)}

.divider{left:581px;top:210px;height:790px;border-left:1px dotted #c8c8c8}

.post{position:absolute;left:36px;width:517px}
.date{position:absolute;left:0;top:0;width:67px;height:60px;background:var(--navy);color:var(--gold);text-align:center;font-family:"Roboto",sans-serif}
.date .day{font-size:31px;font-weight:300;line-height:1;padding-top:6px;display:block}
.date .month{font-size:12px;display:block;margin-top:1px}
.post-body{position:absolute;left:75px;top:-3px;width:442px}
.post-title{font-family:"Roboto",sans-serif;font-weight:300;font-size:16.5px;color:var(--navy);line-height:20px}
.meta{font-size:9.5px;color:#444;line-height:12px;position:relative}
.meta b{color:var(--navy);font-weight:400}
.meta .count{position:absolute;right:0;top:0}
.meta a{color:var(--navy);text-decoration:underline}
.excerpt{font-size:10.5px;line-height:14px;color:#333;margin-top:4px}

.pager{top:996px;font-family:"Roboto",sans-serif;font-weight:300;font-size:13px;color:var(--navy);display:flex;align-items:center;gap:7px}
.pager .btn{width:19px;height:19px;background:var(--navy);display:flex;align-items:center;justify-content:center}

.sidebar-title{left:618px;top:225px;font-family:"Roboto",sans-serif;font-size:12px;color:var(--navy)}
.search{left:618px;top:245px;width:211px;height:30px;background:var(--panel);font-size:9px;color:#555;padding:10px 11px}
.promo{left:618px;width:212px;border:3px solid #4b5b9e;background:#fff;overflow:hidden}
.promo .ph{position:absolute}
.promo .txt{position:absolute;font-family:"Roboto",sans-serif;font-weight:700}

.footer{left:0;top:1050px;width:892px;height:120px;background:var(--footer)}
.footer .col-rule{position:absolute;top:0;width:1px;height:120px;background:#2c2d2f}
.footer .label{position:absolute;left:42px;top:14px;font-family:"Roboto",sans-serif;font-size:11px;color:#fff}
.footer .big{position:absolute;left:40px;top:34px;font-family:"Roboto",sans-serif;font-weight:300;font-size:46px;color:#d9d9d9;line-height:1}
.footer .sub{position:absolute;left:47px;top:84px;font-family:"Roboto",sans-serif;font-size:10.5px;color:#d0d0d0}
.footer .ftitle{position:absolute;left:130px;top:24px;font-family:"Roboto",sans-serif;font-size:14.5px;color:#e5e5e5}
.footer .fexc{position:absolute;left:130px;top:55px;width:470px;white-space:nowrap;overflow:hidden;font-family:"Roboto",sans-serif;font-size:10px;color:#8a8a8a}
.footer .more{position:absolute;left:130px;top:72px;font-family:"Roboto",sans-serif;font-size:11px;color:var(--gold)}
.footer .arrows{position:absolute;left:672px;top:27px;display:flex;gap:12px}
.finfo{position:absolute;left:741px;font-family:"Roboto",sans-serif;font-size:10px;color:#e0e0e0;display:flex;align-items:center;gap:8px}
.finfo i{width:18px;height:18px;border-radius:50%;background:#d7d7d7;display:block}
.bottom{left:0;top:1170px;width:892px;height:30px;background:var(--footer-deep);font-family:"Roboto",sans-serif;font-size:9.5px;color:#bdbdbd}
.bottom span{position:absolute;top:10px}
</style>
</head>
<body>

<div class="abs topbar">
  <div class="contact" style="left:558px">
    <svg width="9" height="9" viewBox="0 0 10 10"><path d="M2 0.5 L4 2.8 L3 4 Q4.5 6 6 7 L7.2 6 L9.5 8 L8 9.6 Q3.5 9 0.5 2 Z" fill="#ffffff"/></svg>
    (555) 010-4821
  </div>
  <div class="contact" style="left:651px">
    <svg width="10" height="8" viewBox="0 0 10 8"><rect x="0.5" y="0.5" width="9" height="7" fill="#fff"/><path d="M0.5 0.5 L5 4.5 L9.5 0.5" fill="none" stroke="#2e3033"/></svg>
    info@brivolt.example
  </div>
  <div class="social" aria-label="Social links"><span></span><span></span><span></span><span></span><span></span></div>
</div>

<header class="abs header">
  <div class="brand">
    <span class="mark"></span>
    <span class="name">Brivolt Data</span>
    <span class="tag">Enterprise Data Quality Made Easy</span>
  </div>
  <nav class="nav">
    <span>Home</span><span class="current">Connectors</span><span>Features</span><span>Why QualiSync?</span><span>Offers</span><span>Services</span><span>Blog</span><span>About Us</span>
  </nav>
</header>

<div class="abs banner"><h1>Blog</h1></div>
<div class="abs banner-rule"></div>

<div class="abs divider"></div>

<article class="post" style="top:251px">
  <div class="date"><span class="day">02</span><span class="month">October</span></div>
  <div class="post-body">
    <h2 class="post-title">Welcome to the Brivolt Data Blog</h2>
    <p class="meta">Posted by <b>Brivolt Data</b><span class="count">1 Comment (s)</span><br>Tags: <a>Address Verification</a>, <a>Blog</a>, <a>Data Cleaning</a>, <a>Data Quality</a>, <a>Duplicate Records</a></p>
    <p class="excerpt">QualiSync data quality software provides a single solution for all of your address validation needs.</p>
  </div>
</article>

<article class="post" style="top:347px">
  <div class="date"><span class="day">17</span><span class="month">September</span></div>
  <div class="post-body">
    <h2 class="post-title">They Can’t Find My Record</h2>
    <p class="meta">Posted by <b>Brivolt Data</b><span class="count">1 Comment (s)</span><br>Tags: <a>Data Cleaning</a></p>
    <p class="excerpt">I called one of the major PC vendors recently to purchase a new laptop. We had purchased from them several times before. The sales rep on the phone asked me if I knew my customer number. I didn’t. He exhaled as though exhausted and asked me if I could find it.</p>
  </div>
</article>

<article class="post" style="top:466px">
  <div class="date"><span class="day">17</span><span class="month">September</span></div>
  <div class="post-body">
    <h2 class="post-title">Cras Data Cleaning</h2>
    <p class="meta">Posted by <b>Brivolt Data</b><span class="count">1 Comment (s)</span><br>Tags: <a>Data Cleaning</a></p>
    <p class="excerpt">Cras vestibulum leo quis rutrum dignissim. Vivamus eu mauris lacus. Nullam sit amet congue erat. Nulla fermentum purus non dui rhoncus, vitae luctus tortor congue. Nam congue, tellus sit amet tristique vestibulum, justo velit pulvinar lorem, et pretium lectus elit sed nisi. Donec volutpat condimentum elit, at rhoncus sapien laoreet a. Sed sed velit ultricies</p>
  </div>
</article>

<article class="post" style="top:598px">
  <div class="date"><span class="day">17</span><span class="month">September</span></div>
  <div class="post-body">
    <h2 class="post-title">Praesent Data</h2>
    <p class="meta">Posted by <b>Brivolt Data</b><span class="count">1 Comment (s)</span><br>Tags: <a>Data Quality</a></p>
    <p class="excerpt">Praesent quis nunc venenatis, viverra diam in, fringilla turpis. Maecenas convallis nibh consequat nunc vulputate, ac adipiscing justo bibendum. Morbi posuere elit eget risus faucibus aliquam. Mauris scelerisque nisi eu tortor fermentum pulvinar.</p>
  </div>
</article>

<article class="post" style="top:723px">
  <div class="date"><span class="day">17</span><span class="month">September</span></div>
  <div class="post-body">
    <h2 class="post-title">Data Vestibulum Ipsum</h2>
    <p class="meta">Posted by <b>Brivolt Data</b><span class="count">1 Comment (s)</span><br>Tags: <a>Data Quality</a></p>
    <p class="excerpt">Vestibulum ipsum nulla, rhoncus eu nibh in, aliquet rutrum neque. Praesent hendrerit sem in dui scelerisque, eu tincidunt turpis sollicitudin. Nam ante nisi, scelerisque sed nunc et, interdum rhoncus augue.</p>
  </div>
</article>

<article class="post" style="top:838px">
  <div class="date"><span class="day">17</span><span class="month">September</span></div>
  <div class="post-body">
    <h2 class="post-title">Finding and Merging Duplicate Records</h2>
    <p class="meta">Posted by <b>Brivolt Data</b><span class="count">1 Comment (s)</span><br>Tags: <a>featured</a>, <a>featured_pages</a>, <a>Home</a></p>
    <p class="excerpt">QualiSync accurately matches duplicate records and intelligently merges them into a single best record.</p>
  </div>
</article>

<div class="abs pager" style="left:107px">
  <span class="btn"><svg width="9" height="11" viewBox="0 0 9 11"><path d="M7 1 L2 5.5 L7 10" fill="none" stroke="#f5b81c" stroke-width="2.5"/></svg></span>Previous
</div>
<div class="abs pager" style="left:499px">
  Next<span class="btn"><svg width="9" height="11" viewBox="0 0 9 11"><path d="M2 1 L7 5.5 L2 10" fill="none" stroke="#f5b81c" stroke-width="2.5"/></svg></span>
</div>

<aside>
  <div class="abs sidebar-title">Search Our Blog</div>
  <div class="abs search">Enter the keyword...</div>

  <div class="abs promo" style="top:305px;height:176px">
    <div class="txt" style="left:0;width:206px;top:6px;text-align:center;font-size:18px;color:var(--navy)">QualiSync</div>
    <div class="txt" style="left:0;width:206px;top:29px;text-align:center;font-size:15px;color:var(--navy)">Address Correction</div>
    <div class="ph" role="img" aria-label="Photo grid of business people on a blue tiled wall" style="left:0;top:58px;width:206px;height:112px;background:linear-gradient(135deg,#3f55a6,#1f2c63)"></div>
    <div class="txt" style="left:8px;top:60px;background:var(--gold);color:#fff;font-size:12px;padding:2px 6px">Try it for Free</div>
    <div class="txt" style="right:6px;top:150px;color:#fff;font-size:11px;font-weight:500">Brivolt Data</div>
  </div>

  <div class="abs promo" style="top:508px;height:177px">
    <div class="ph" role="img" aria-label="Keyboard with a thumbs-up businessman" style="left:110px;top:0;width:96px;height:100px;background:linear-gradient(160deg,#2a3775,#6a7aa8)"></div>
    <div class="txt" style="left:10px;top:16px;width:110px;font-size:13.5px;font-weight:500;line-height:18px;color:var(--navy-dark)">Find out how far you can get in just two days using</div>
    <div class="txt" style="left:10px;top:92px;font-size:15px;color:var(--navy-dark)">QualiSync</div>
    <div class="txt" style="left:118px;top:96px;background:var(--gold);color:#fff;font-size:12px;padding:2px 6px">Click Here</div>
    <div class="txt" style="left:50px;top:122px;font-size:16px;color:var(--navy-dark)">Proof of Concept</div>
    <div class="txt" style="right:8px;top:148px;color:var(--navy);font-size:11px;font-weight:500">Brivolt Data</div>
  </div>

  <div class="abs promo" style="top:716px;height:176px;background:var(--navy)">
    <div class="ph" role="img" aria-label="Colleagues working together at a desk" style="left:0;top:0;width:206px;height:62px;background:linear-gradient(90deg,#6d6a66,#c9c5bf)"></div>
    <div class="txt" style="left:94px;top:28px;width:112px;height:30px;background:#fff"></div>
    <div class="txt" style="left:160px;top:16px;background:var(--gold);color:#fff;font-size:11px;padding:1px 6px">Free</div>
    <div class="txt" style="left:98px;top:33px;font-size:15.5px;color:#111">White Paper</div>
    <div class="ph" style="left:84px;top:72px;width:26px;height:34px;background:#e8e8e8"></div>
    <div class="txt" style="left:118px;top:70px;width:86px;font-size:12.5px;line-height:16px;color:#fff;text-align:center">10 Questions to Ask when Evaluating</div>
    <div class="txt" style="left:10px;top:120px;font-size:15px;color:#fff">Data Quality Solutions</div>
    <div class="txt" style="left:10px;top:149px;background:#111;color:#fff;font-size:13px;padding:1px 6px">Click Here</div>
    <div class="txt" style="right:8px;top:151px;color:#fff;font-size:11px;font-weight:500">Brivolt Data</div>
  </div>
</aside>

<footer class="abs footer">
  <span class="col-rule" style="left:111px"></span>
  <span class="col-rule" style="left:725px"></span>
  <div class="label">Latest Posts</div>
  <div class="big">02</div>
  <div class="sub">Oct&nbsp; 2013</div>
  <div class="ftitle">Welcome to the Brivolt Data Blog</div>
  <div class="fexc">The goal of this blog is to share our experiences, educate and sometimes entertain. Computers, ente</div>
  <div class="more">Read More</div>
  <div class="arrows">
    <svg width="9" height="11" viewBox="0 0 9 11"><path d="M7 1 L2 5.5 L7 10" fill="none" stroke="#fff" stroke-width="2"/></svg>
    <svg width="9" height="11" viewBox="0 0 9 11"><path d="M2 1 L7 5.5 L2 10" fill="none" stroke="#fff" stroke-width="2"/></svg>
  </div>
  <div class="finfo" style="top:20px"><i></i>0 Comments</div>
  <div class="finfo" style="top:50px"><i></i>Lumenforge</div>
  <div class="finfo" style="top:80px"><i></i>Share</div>
</footer>

<div class="abs bottom">
  <span style="left:38px">QualiSync is easy to use, enterprise data quality software.</span>
  <span style="right:30px">Copyright © 2013 Brivolt Data | Email Us</span>
</div>

</body>
</html>
```